Elevating our current Business Card Design

We want to elevate our current business card with a new design to look like a zenith 300 company. We are a premium lubricant distributor (oil and grease).
We need 2 versions, version 1 is as per the uploaded a copy of our current business card with the English version.
For our Chinese version we need to use the front to be English in English and have the back of the card designed exactly like the front for all info to be in Chinese.
The design template needs to be such that we can amend the template with adding different information for each person's card.
The background colour of the card can be changed- we just need to clearly see all information on the card and logos.
The QJR and Ember steady logos cannot have any colour or display changes- only use the logos attached.
All logos need to be included and all information from the attached current card

```html
<!DOCTYPE html>
<html lang="en">
<head>
<meta charset="utf-8">
<title>Meridian Lubricant Distributors – Business Card</title>
<link href="https://fonts.googleapis.com/css2?family=Open+Sans:wght@400;600;700;800&display=swap" rel="stylesheet">
<style>
  :root {
    --backdrop: #222222;
    --gold: #d29e2a;
    --gold-light: #e3b53c;
    --gold-stripe: #e2ad2c;
    --red: #ee2e24;
    --red-deep: #8f141a;
    --white: #ffffff;
    --ink: #1d1d1d;
    --cert-orange: #f0731c;
    --cert-grey: #8a8a8a;
    --eco-green: #1f4a34;
  }
  * { box-sizing: border-box; margin: 0; padding: 0; }
  html, body {
    width: 1200px; height: 780px; overflow: hidden;
    background: var(--backdrop);
    font-family: "Open Sans", Arial, sans-serif;
  }
  .stage {
    width: 1200px; height: 780px;
    display: flex; align-items: center; justify-content: center; gap: 40px;
  }
  .card {
    position: relative;
    width: 520px; height: 300px;
    border-radius: 18px;
    overflow: hidden;
  }

  /* Front */
  .card-front {
    background: radial-gradient(ellipse at 45% 40%, var(--gold-light), var(--gold) 70%);
  }
  .front-pattern {
    position: absolute; inset: 0;
    background: linear-gradient(135deg, rgba(255,230,120,0.18), rgba(160,110,20,0.12));
  }
  .front-brand {
    position: absolute; inset: 0;
    display: flex; align-items: center; justify-content: center; gap: 16px;
  }
  .front-brand-dot {
    width: 46px; height: 46px; border-radius: 50%;
    background: var(--white);
  }
  .front-brand-name {
    font-size: 46px; font-weight: 700; color: var(--red);
    letter-spacing: 1px;
  }

  /* Back */
  .card-back { background: var(--white); }
  .back-swoosh { position: absolute; inset: 0; }
  .holder {
    position: absolute; right: 28px; top: 22px;
    text-align: right; color: var(--white);
  }
  .holder-name { font-size: 24px; font-weight: 600; line-height: 1.15; }
  .holder-title { font-size: 13px; font-weight: 400; }

  .address {
    position: absolute; left: 28px; top: 168px;
    font-size: 12.5px; line-height: 1.35; color: var(--ink);
  }
  .contacts {
    position: absolute; left: 28px; top: 210px;
    list-style: none; font-size: 12.5px; color: var(--ink);
  }
  .contacts li { display: flex; align-items: center; gap: 8px; height: 17px; }
  .contacts svg { width: 12px; height: 12px; flex: none; }

  .partners {
    position: absolute; right: 18px; bottom: 22px;
    width: 250px; height: 118px;
  }
  .eco-badge {
    position: absolute; left: 0; top: 26px;
    width: 58px; height: 36px; border-radius: 18px 18px 6px 6px;
    background: var(--eco-green);
  }
  .cert-badges {
    position: absolute; left: 70px; top: 0;
    display: flex; gap: 14px;
  }
  .cert-badge {
    width: 44px; height: 44px; border-radius: 50%;
    background: var(--cert-orange);
    border: 4px solid var(--cert-grey);
  }
  .distributor-box {
    position: absolute; left: 0; bottom: 0;
    width: 150px; height: 46px;
    border: 1.5px solid var(--red);
    display: flex; align-items: center; gap: 6px; padding: 0 8px;
  }
  .distributor-dot {
    width: 10px; height: 10px; border-radius: 50%; background: var(--gold); flex: none;
  }
  .distributor-name {
    font-size: 8.5px; font-weight: 600; line-height: 1.2; color: var(--red);
    text-transform: uppercase;
  }
  .supplier-block {
    position: absolute; right: 0; bottom: 18px;
    width: 100px; height: 46px;
    background: var(--red); color: var(--white);
    display: flex; flex-direction: column; justify-content: center; align-items: center;
  }
  .supplier-name { font-size: 15px; font-weight: 800; letter-spacing: 0.5px; line-height: 1.1; }
  .supplier-line { font-size: 6.5px; font-weight: 800; letter-spacing: 0.3px; }
</style>
</head>
<body>
<main class="stage">

  <section class="card card-front" aria-label="Card front">
    <div class="front-pattern" role="img" aria-label="Embossed gold repeating motif background"></div>
    <div class="front-brand">
      <span class="front-brand-dot"></span>
      <span class="front-brand-name">Meridian</span>
    </div>
  </section>

  <section class="card card-back" aria-label="Card back">
    <svg class="back-swoosh" viewBox="0 0 520 300" preserveAspectRatio="none" aria-hidden="true">
      <defs>
        <linearGradient id="bandRed" x1="0" y1="1" x2="1" y2="0">
          <stop offset="0" stop-color="var(--red)"/>
          <stop offset="0.55" stop-color="var(--red)"/>
          <stop offset="1" stop-color="var(--red-deep)"/>
        </linearGradient>
      </defs>
      <path d="M0 0 H520 V82 C480 125 380 138 250 140 C140 142 50 140 0 150 Z" fill="url(#bandRed)"/>
      <path d="M520 82 C480 125 380 138 250 140 C140 142 50 140 0 150 V160 C50 146 140 148 250 146 C390 143 485 130 520 92 Z" fill="var(--gold-stripe)"/>
    </svg>

    <div class="holder">
      <p class="holder-name">Maren Talbot</p>
      <p class="holder-title">Administration Executive</p>
    </div>

    <p class="address">48 Freightway Drive<br>Harlow Park, WA 6190</p>

    <ul class="contacts">
      <li>
        <svg viewBox="0 0 12 12"><path d="M2 1 L4 1 L5 4 L3.5 5 C4.3 6.8 5.2 7.7 7 8.5 L8 7 L11 8 L11 10 C11 10.6 10.6 11 10 11 C5 11 1 7 1 2 C1 1.4 1.4 1 2 1 Z" fill="var(--red)"/></svg>
        1300 000 417
      </li>
      <li>
        <svg viewBox="0 0 12 12"><rect x="3" y="0.8" width="6" height="10.4" rx="1.2" fill="none" stroke="var(--red)" stroke-width="1.2"/><circle cx="6" cy="9.4" r="0.7" fill="var(--red)"/></svg>
        +61 400 000 218
      </li>
      <li>
        <svg viewBox="0 0 12 12"><rect x="1" y="4" width="10" height="7" rx="1" fill="var(--red)"/><rect x="3" y="1" width="6" height="4" fill="none" stroke="var(--red)" stroke-width="1"/><rect x="3" y="6" width="6" height="1" fill="var(--white)"/><rect x="3" y="8" width="6" height="1" fill="var(--white)"/></svg>
        +61 8 9000 4521
      </li>
      <li>
        <svg viewBox="0 0 12 12"><circle cx="6" cy="6" r="5" fill="none" stroke="var(--red)" stroke-width="1.2"/><ellipse cx="6" cy="6" rx="2" ry="5" fill="none" stroke="var(--red)" stroke-width="1"/><line x1="1" y1="6" x2="11" y2="6" stroke="var(--red)" stroke-width="1"/></svg>
        www.meridianlube.example
      </li>
      <li>
        <svg viewBox="0 0 12 12"><rect x="1" y="3" width="10" height="7" rx="0.8" fill="var(--red)"/><path d="M1.5 3.5 L6 7 L10.5 3.5" fill="none" stroke="var(--white)" stroke-width="1"/></svg>
        m.talbot@meridianlube.example
      </li>
    </ul>

    <div class="partners">
      <div class="eco-badge" role="img" aria-label="Ember steady network member badge"></div>
      <div class="cert-badges">
        <div class="cert-badge" role="img" aria-label="QJR ISO certification badge"></div>
        <div class="cert-badge" role="img" aria-label="QJR ISO certification badge"></div>
        <div class="cert-badge" role="img" aria-label="QJR ISO certification badge"></div>
      </div>
      <div class="distributor-box">
        <span class="distributor-dot"></span>
        <span class="distributor-name">Meridian Lubricant<br>Distributors</span>
      </div>
      <div class="supplier-block">
        <span class="supplier-name">KORVANE</span>
        <span class="supplier-line">PREMIUM LUBRICANTS</span>
      </div>
    </div>
  </section>

</main>
</body>
</html>
```